Road Construction Company needs business cards

We would like a new business card designed for our business.

We're a road construction company based in Qld, Australia.

Can the business card please have the following information on it.

Name: Warren Halbeck
Position: General Manager
Phone: 0472 915 348
Email: Warren.halbeck@tovrin.com.au
Address: 87 Marrow Ave, Pendlebay, QLD, 4023
Website: www.tovrin.com.au

Visually we'd like the card to be professional and simple.

Attached is our logo.

Our website is www.tovrin.com.au

Target Market(s)

Men aged 25-60

Contact Information for Business Card

As listed in project description

Font styles to use
Serif

Requirements
Must have
• Large logo on back of card

```html
<!DOCTYPE html>
<html lang="en">
<head>
<meta charset="utf-8">
<title>Tovrin Business Card</title>
<link rel="stylesheet" href="https://fonts.googleapis.com/css2?family=Krona+One&family=Play:wght@400;700&display=swap">
<style>
  :root {
    --page-bg: #2a2a2a;
    --brand-blue: #0356a5;
    --accent-blue: #34a8dd;
    --card-white: #ffffff;
    --ink-light: #ffffff;
  }
  html, body {
    margin: 0;
    padding: 0;
    width: 1093px;
    height: 1200px;
    overflow: hidden;
    background: var(--page-bg);
  }
  .canvas {
    position: relative;
    width: 1093px;
    height: 1200px;
  }
  .card {
    position: absolute;
    left: 264px;
    width: 580px;
    height: 357px;
    overflow: hidden;
    box-shadow: 3px 4px 6px rgba(0,0,0,0.6);
  }
  .card-front { top: 226px; background: var(--card-white); }
  .card-back { top: 620px; background: var(--brand-blue); }

  .front-panel {
    position: absolute;
    inset: 0;
    width: 580px;
    height: 357px;
  }
  .contact {
    position: absolute;
    left: 26px;
    top: 132px;
    color: var(--ink-light);
    font-family: "Play", sans-serif;
    font-size: 16px;
    line-height: 21px;
  }
  .contact-name {
    margin: 0;
    font-family: "Krona One", sans-serif;
    font-size: 16px;
    line-height: 20px;
    letter-spacing: 0.5px;
    text-transform: uppercase;
  }
  .contact-role { margin: 0 0 14px; }
  .contact-address { margin: 0 0 13px; font-style: normal; }
  .contact-list { list-style: none; margin: 0; padding: 0; }
  .contact-list li {
    display: flex;
    align-items: center;
    gap: 7px;
  }
  .contact-icon { width: 15px; height: 15px; flex: none; }

  .brand-name {
    position: absolute;
    margin: 0;
    font-family: "Play", sans-serif;
    font-weight: 700;
    text-transform: uppercase;
    letter-spacing: 3px;
    line-height: 1;
    white-space: nowrap;
    transform: translate(-50%, -50%);
  }
  .brand-name-front {
    left: 426px;
    top: 100px;
    font-size: 40px;
    color: var(--brand-blue);
  }
  .brand-name-back {
    left: 290px;
    top: 176px;
    font-size: 62px;
    color: var(--ink-light);
  }
</style>
</head>
<body>
<div class="canvas">

  <section class="card card-front">
    <svg class="front-panel" viewBox="0 0 580 357" aria-hidden="true">
      <polygon points="0,0 218,0 345,357 0,357" fill="var(--brand-blue)"/>
      <polygon points="222,0 228,0 357,357 350,357" fill="var(--accent-blue)"/>
    </svg>

    <div class="contact">
      <h1 class="contact-name">Warren Halbeck</h1>
      <p class="contact-role">General Manager</p>
      <address class="contact-address">87 Marrow Ave<br>Pendlebay, QLD, 4023</address>
      <ul class="contact-list">
        <li>
          <svg class="contact-icon" viewBox="0 0 16 16" aria-hidden="true">
            <path d="M3.5 1.5l2.3 2.6-1.3 1.8c.9 2 2.6 3.7 4.6 4.6l1.8-1.3 2.6 2.3-1.4 2.2C7.5 14.6 1.4 8.5 1.3 3z" fill="none" stroke="#fff" stroke-width="1.6" stroke-linejoin="round"/>
            <path d="M9.5 2.5a4 4 0 0 1 4 4M9.5 5a1.5 1.5 0 0 1 1.5 1.5" fill="none" stroke="#fff" stroke-width="1.3"/>
          </svg>
          <span>0472 915 348</span>
        </li>
        <li>
          <svg class="contact-icon" viewBox="0 0 16 16" aria-hidden="true">
            <rect x="0.5" y="3" width="15" height="10" fill="#fff"/>
            <path d="M0.5 3l7.5 6 7.5-6M0.5 13l5.5-5M15.5 13l-5.5-5" fill="none" stroke="var(--brand-blue)" stroke-width="1.2"/>
          </svg>
          <span>Warren.halbeck@tovrin.com.au</span>
        </li>
        <li>
          <svg class="contact-icon" viewBox="0 0 16 16" aria-hidden="true">
            <circle cx="8" cy="8" r="6.8" fill="none" stroke="#fff" stroke-width="1.3"/>
            <ellipse cx="8" cy="8" rx="3" ry="6.8" fill="none" stroke="#fff" stroke-width="1.1"/>
            <path d="M1.2 8h13.6M2.2 4.6h11.6M2.2 11.4h11.6" stroke="#fff" stroke-width="1.1"/>
          </svg>
          <span>www.tovrin.com.au</span>
        </li>
      </ul>
    </div>

    <p class="brand-name brand-name-front">Tovrin</p>
  </section>

  <section class="card card-back">
    <p class="brand-name brand-name-back">Tovrin</p>
  </section>

</div>
</body>
</html>
```